University Student Business Card

Looking for a professional university student business card. Student is studying business with a focus on marketing. Some combination using a monogram and/or full name on the front with full name, university details and contact information on the back. Card should be modern design for a young professional. Prefer use of royal blue, black and white but am open to other uses of colour palette if it reinforces young/trendy style. Initials for a monogram are: KR. Full details will be provided in private consultation with designer(s).

Target Market(s)

Professional business people, marketers, advertisers, consultants

Industry/Entity Type

Business, marketing

Contact Information for Business Card

Monogram or personal logo, full name, university name, program of study, phone number, email address, pathfolio address

Other font styles liked:
• Open to suggestion to fulfill above requirements

Colors
0054AA
0677BA
7BADD7
CADEEF
E8F1F8

Requirements
Must have
• Monogram using letters K and R, and incorporate the business card details listed in the brief (specific details including personal contact info will be shared with successful designer to ensure privacy)
Nice to have
• Personal brand using monogram or personal logo (not a business logo)

```html
<!DOCTYPE html>
<html lang="en">
<head>
<meta charset="utf-8">
<title>Jordan Hale – Business Card</title>
<link rel="stylesheet" href="https://fonts.googleapis.com/css2?family=Montserrat:wght@500;600;700;800&family=Arimo:wght@400&display=swap">
<style>
  :root {
    --backdrop: #2d2d2d;
    --paper: #ffffff;
    --ink: #0b1a33;
    --royal: #0054aa;
    --royal-bright: #0a5fb3;
    --royal-deep: #001a3d;
    --text-dark: #1c1c1c;
    --rule-light: #9aa3ad;
    --rule-dark: rgba(255,255,255,0.45);
    --pathfolio-dot: #0677ba;
  }
  * { box-sizing: border-box; margin: 0; padding: 0; }
  html, body {
    width: 1200px; height: 866px; overflow: hidden;
    background: var(--backdrop);
  }
  .sheet {
    width: 1200px; height: 866px;
    display: flex; align-items: center; justify-content: center; gap: 40px;
  }
  .card {
    width: 540px; height: 309px;
    display: flex; flex-direction: column; align-items: center; justify-content: center;
    text-align: center;
    box-shadow: 0 10px 24px rgba(0,0,0,0.45);
  }
  /* Front */
  .card--front { background: var(--paper); }
  .monogram {
    font-family: "Montserrat", sans-serif;
    font-weight: 800;
    font-size: 74px;
    line-height: 1;
    color: var(--ink);
    letter-spacing: 2px;
    margin-bottom: 14px;
  }
  .holder-name {
    font-family: "Montserrat", sans-serif;
    font-weight: 700;
    font-size: 26px;
    color: var(--royal);
    letter-spacing: 1px;
    text-transform: uppercase;
  }
  .programme {
    font-family: "Arimo", sans-serif;
    font-size: 17px;
    color: var(--text-dark);
    margin-top: 4px;
  }
  .rule {
    width: 90px; height: 1px;
    background: var(--rule-light);
    margin: 12px auto;
  }
  .profile-link {
    display: flex; align-items: center; gap: 10px;
    font-family: "Arimo", sans-serif;
    font-size: 17px;
    color: var(--text-dark);
  }
  .profile-link__dot {
    width: 20px; height: 20px; border-radius: 50%;
    background: var(--pathfolio-dot);
  }
  /* Back */
  .card--back {
    background: radial-gradient(ellipse at 45% 45%, var(--royal-bright) 0%, var(--royal) 40%, var(--royal-deep) 100%);
    color: #ffffff;
  }
  .university-name {
    font-family: "Montserrat", sans-serif;
    font-weight: 700;
    font-size: 27px;
    letter-spacing: 2px;
    text-transform: uppercase;
  }
  .card--back .rule { background: var(--rule-dark); margin: 10px auto; }
  .contact-block {
    font-family: "Arimo", sans-serif;
    font-size: 16px;
    line-height: 1.35;
    letter-spacing: 0.5px;
  }
</style>
</head>
<body>
  <main class="sheet">
    <section class="card card--front" aria-label="Card front">
      <div class="monogram">KR</div>
      <h1 class="holder-name">Jordan Hale</h1>
      <p class="programme">Business Marketing</p>
      <div class="rule"></div>
      <p class="profile-link"><span class="profile-link__dot"></span>pathfolio.com/name</p>
    </section>

    <section class="card card--back" aria-label="Card back">
      <h2 class="university-name">University Name</h2>
      <div class="rule"></div>
      <p class="contact-block">421, Address line goes here<br>45452, Country Name</p>
      <div class="rule"></div>
      <p class="contact-block">055-210 338 417<br>hello@jordanhale.net<br>www.jordanhale.net</p>
    </section>
  </main>
</body>
</html>
```